business card for a massage therapy practice named 'Cedar and Willow Massage Studio'

I really need a trendy, yet easy on the eyes business card to complement my logo. Ideally with some gold or rose gold foil work.

My uploaded file of the logo I have in horizontal but I have a vertical version as well. Another color that is used in the website is a blush pink here and there. I'd like to see some trendy tropical leaves in the design.

```html
<!DOCTYPE html>
<html lang="en">
<head>
<meta charset="utf-8">
<title>Cedar and Willow Massage Studio — Business Card</title>
<link rel="stylesheet" href="https://fonts.googleapis.com/css2?family=Satisfy&family=Work+Sans:wght@400;500&display=swap">
<style>
  :root {
    --backdrop: #2b2b2c;
    --card: #141414;
    --card-edge: #1d1d1d;
    --gold: #cfa851;
    --gold-soft: #e0c27a;
  }
  * { box-sizing: border-box; margin: 0; padding: 0; }
  html, body {
    width: 1200px; height: 900px; overflow: hidden;
    background: var(--backdrop);
    font-family: "Work Sans", Arial, sans-serif;
    color: var(--gold);
  }
  .canvas {
    position: relative; width: 1200px; height: 900px;
    display: flex; flex-direction: column; align-items: center; justify-content: center; gap: 40px;
  }
  .card {
    position: relative; width: 620px; height: 354px;
    background: linear-gradient(135deg, var(--card-edge), var(--card) 60%);
    border-radius: 3px;
    box-shadow: 0 10px 26px rgba(0,0,0,.45);
  }

  /* front */
  .card-front { display: flex; align-items: center; justify-content: center; gap: 16px; }
  .brand-dot { width: 22px; height: 22px; border-radius: 50%; background: var(--gold); }
  .brand-name {
    font-family: "Work Sans", Arial, sans-serif; font-weight: 500;
    color: var(--gold); text-transform: uppercase; letter-spacing: .16em;
    font-size: 22px; line-height: 1.35;
  }

  /* back */
  .card-back { padding: 34px 0 0 44px; }
  .back-brand { display: flex; align-items: center; gap: 10px; }
  .back-brand .brand-dot { width: 14px; height: 14px; }
  .back-brand .brand-name { font-size: 13px; letter-spacing: .14em; }
  .person-name {
    font-family: "Satisfy", cursive; font-size: 34px; color: var(--gold);
    margin-top: 34px; font-weight: 400;
  }
  .address { font-size: 14px; line-height: 1.45; margin-top: 14px; padding-left: 6px; }
  .contacts { list-style: none; margin-top: 20px; font-size: 15px; line-height: 1.55; }
  .contacts li { display: flex; align-items: center; gap: 8px; }
  .contacts svg { width: 11px; height: 11px; fill: var(--gold); flex: none; }
  .mark-area {
    position: absolute; left: 370px; top: 77px; width: 200px; height: 200px;
    border-radius: 50%;
    background: radial-gradient(circle at 40% 35%, var(--gold-soft), var(--gold) 70%);
  }
</style>
</head>
<body>
<main class="canvas">
  <section class="card card-front" aria-label="Card front">
    <span class="brand-dot"></span>
    <p class="brand-name">Cedar and Willow<br>Massage Studio</p>
  </section>

  <section class="card card-back" aria-label="Card back">
    <div class="back-brand">
      <span class="brand-dot"></span>
      <p class="brand-name">Cedar and Willow<br>Massage Studio</p>
    </div>
    <h1 class="person-name">Marisol Vega</h1>
    <p class="address">418 Laurel Ave. suite 210,<br>Sacramento, CA 95816</p>
    <ul class="contacts">
      <li><svg viewBox="0 0 10 10"><path d="M2 0h2l1 3-1.3 1a6 6 0 0 0 2.3 2.3L7 5l3 1v2a2 2 0 0 1-2 2A8 8 0 0 1 0 2a2 2 0 0 1 2-2z"/></svg>(916) 555-0148</li>
      <li><svg viewBox="0 0 10 10"><path d="M0 2h10v6H0z M0 2l5 3.5L10 2" fill="none" stroke="#cfa851" stroke-width="1.2"/></svg>cedarandwillow@mail.com</li>
      <li><svg viewBox="0 0 10 10"><circle cx="5" cy="5" r="4.3" fill="none" stroke="#cfa851" stroke-width="1.1"/><path d="M.7 5h8.6M5 .7c-2.4 2.6-2.4 6 0 8.6M5 .7c2.4 2.6 2.4 6 0 8.6" fill="none" stroke="#cfa851" stroke-width=".9"/></svg>www.cedarandwillow.com</li>
    </ul>
    <div class="mark-area" role="img" aria-label="Large gold foil brand mark"></div>
  </section>
</main>
</body>
</html>
```